Business card design for a dynamic IT consulting company

We need a business card design for a young firm, specialized in the Telecommunications/Consulting industry. The name of the company is Quindor and Partners Business Consulting Ltd. (Short name: Quindor and Partnes)
Quindor = solve read reverse, so we aim to be uncomplicated and solution-oriented. The small pipe in our logo is also related to the word solve. So we need a new business card design, which is simple, eye catching and something non traditional (I would probably prefer a square shaped design rather than a rectangle, but open for suggestions). Attached our logo.

Target Market(s)

Usually our customers are Tier1 Telecoms providers (Q-Netra, Palorix, etc) and their executives.

Industry/Entity Type

Business

Contact Information for Business Card

Name: Bence Tolnavari
Email: b.tolnavari@quindor.hu
Web: www.quindor.hu
Mobile: +36 30 518 2769
Title: Managing Director

Optional:
Company name: Quindor and Partners Ltd.
Address: 1087 Budapest, Tolvenka str. 28/C, Hungary

Font styles to use
Other font styles liked:
• helveticaneue_medium, Prime Regular are used now.

Colors

Designer to choose colors to be used in the design.

Requirements
Must have
• I would like to have a 2 sided design.
Nice to have
• I thought if we make the logo a bit bigger (without the company name), that could go to the back with the company name below. I though, if the pipe in the logo is somehow touchable on the business card, would be nice and unique.

```html
<!DOCTYPE html>
<html lang="en">
<head>
<meta charset="utf-8">
<title>Quindor &amp; Partners – Business Card</title>
<link rel="stylesheet" href="https://fonts.googleapis.com/css2?family=Arimo:wght@400;700&display=swap">
<style>
  :root {
    --backdrop: #5b4939;
    --card: #f4f4f4;
    --ink: #58585a;
    --blue: #1a8fd2;
    --magenta: #a8217f;
    --grey: #57575a;
  }
  * { margin: 0; padding: 0; box-sizing: border-box; }
  html, body { width: 1200px; height: 960px; overflow: hidden; }
  body {
    background: var(--backdrop);
    font-family: "Arimo", Arial, sans-serif;
    position: relative;
  }
  .card {
    position: absolute;
    top: 309px;
    width: 342px;
    height: 343px;
    background: var(--card);
    box-shadow: 1px 2px 3px rgba(0,0,0,0.45);
    overflow: hidden;
  }
  .card-front { left: 235px; }
  .card-back  { left: 623px; }

  .brand {
    position: absolute;
    left: 0; right: 0;
    top: 190px;
    display: flex;
    justify-content: center;
    align-items: center;
    gap: 8px;
  }
  .brand-mark {
    width: 10px; height: 10px;
    background: var(--magenta);
  }
  .brand-name {
    font-size: 27px;
    font-weight: 400;
    color: var(--ink);
    letter-spacing: 0.2px;
  }

  .corner { position: absolute; width: 34px; height: 34px; }
  .corner-tl { top: 0; left: 0; }
  .corner-tr { top: 0; right: 0; }
  .corner-bl { bottom: 0; left: 0; }
  .corner-br { bottom: 0; right: 0; }

  .details {
    position: absolute;
    left: 0; right: 0;
    top: 85px;
    text-align: center;
    color: var(--ink);
  }
  .person-name {
    font-size: 19px;
    font-weight: 700;
    color: var(--blue);
    line-height: 22px;
  }
  .person-title {
    font-size: 15px;
    line-height: 19px;
    letter-spacing: 0.3px;
  }
  .address {
    margin-top: 10px;
    font-size: 14px;
    line-height: 18px;
  }
  .contacts {
    margin-top: 11px;
    font-size: 14px;
    line-height: 18px;
    list-style: none;
  }
  .contacts li {
    display: flex;
    justify-content: center;
    align-items: center;
    gap: 3px;
  }
  .contacts svg { flex: none; }
</style>
</head>
<body>
  <section class="card card-front" aria-label="Card front">
    <div class="brand">
      <span class="brand-mark"></span>
      <span class="brand-name">Quindor &amp; Partners</span>
    </div>
  </section>

  <section class="card card-back" aria-label="Card back">
    <svg class="corner corner-tl" viewBox="0 0 34 34"><polygon points="0,0 34,0 0,34" fill="var(--magenta)"/></svg>
    <svg class="corner corner-tr" viewBox="0 0 34 34"><polygon points="0,0 34,0 34,34" fill="var(--grey)"/></svg>
    <svg class="corner corner-bl" viewBox="0 0 34 34"><polygon points="0,0 34,34 0,34" fill="var(--grey)"/></svg>
    <svg class="corner corner-br" viewBox="0 0 34 34"><polygon points="34,0 34,34 0,34" fill="var(--blue)"/></svg>

    <div class="details">
      <h1 class="person-name">BENCE TOLNAVARI</h1>
      <p class="person-title">MANAGING DIRECTOR</p>
      <p class="address">Quindor and Partners Ltd.<br>1087 Budapest<br>Tolvenka str. 28/C, Hungary</p>
      <ul class="contacts">
        <li>
          <svg width="9" height="14" viewBox="0 0 9 14"><rect x="0.8" y="0.8" width="7.4" height="12.4" rx="1.2" fill="none" stroke="var(--blue)" stroke-width="1.5"/><rect x="3" y="10.5" width="3" height="1.2" fill="var(--blue)"/></svg>
          <span>+36 30 518 2769</span>
        </li>
        <li>
          <svg width="12" height="9" viewBox="0 0 12 9"><rect width="12" height="9" fill="var(--blue)"/><polyline points="0.5,0.8 6,5 11.5,0.8" fill="none" stroke="var(--card)" stroke-width="1"/></svg>
          <span>b.tolnavari@quindor.hu</span>
        </li>
        <li>
          <svg width="12" height="12" viewBox="0 0 12 12"><circle cx="6" cy="6" r="6" fill="var(--blue)"/><ellipse cx="6" cy="6" rx="2.5" ry="5.5" fill="none" stroke="var(--card)" stroke-width="0.8"/><line x1="0.5" y1="6" x2="11.5" y2="6" stroke="var(--card)" stroke-width="0.8"/></svg>
          <span>www.quindor.hu</span>
        </li>
      </ul>
    </div>
  </section>
</body>
</html>
```